Fresh, modern, fun business card for pediatric dental practice

Need a business card for fresh, modern, fun pediatric dental practice

Clean look that matches our website's font and colors

We prefer the look of curved corners on business cards

Target Market(s)

parents (mothers) of young children, professionals, mid-high class

Industry/Entity Type

Dental

Contact Information for Business Card

Maplebrook Pediatric Dentistry
482 Quarry Lane
Suite 517
Ashvale, PA 17580
717.555.0193
www.maplebrookkidsdental.example

Mei-Ran Tsai, DMD
Corinne Walbeck, DMD
(we are working on our email address, but we would like that on the card as well)

Font styles to use
Sans Serif

Requirements
Must have
• All info; we would also like to make cards for individual staff members
• colors from our website and color palatte, attatched
• use same font and design as website for branding
Nice to have
• clean, simple card that has a pop of color
• we would like to see a few designs with our tag line "where smiles get brighter"
• we are not sure if we want to have it on there or not
• we would like to see a few designs incorporating the ribbon graphic on our website where the word WELCOME is

```html
<!DOCTYPE html>
<html lang="en">
<head>
<meta charset="utf-8">
<title>Maplebrook Pediatric Dentistry – Business Card</title>
<link rel="stylesheet" href="https://fonts.googleapis.com/css2?family=Roboto:wght@400&family=Roboto+Condensed:wght@700&family=Open+Sans:wght@600&display=swap">
<style>
  :root {
    --backdrop: #2a2a2a;
    --magenta: #d4338f;
    --sun-yellow: #f7b924;
    --paper: #f2f2f2;
    --white: #ffffff;
  }
  * { margin: 0; padding: 0; box-sizing: border-box; }
  html, body { width: 1200px; height: 960px; overflow: hidden; }
  body { background: var(--backdrop); position: relative; font-family: "Roboto", Arial, sans-serif; }

  .card { position: absolute; left: 320px; width: 600px; border-radius: 18px; overflow: hidden; }

  /* Front */
  .card-front { top: 105px; height: 345px; background: var(--magenta); }
  .front-mark { position: absolute; left: 0; right: 0; top: 128px; display: flex; align-items: center; justify-content: center; gap: 14px; }
  .front-mark .dot { width: 26px; height: 26px; border-radius: 50%; background: var(--sun-yellow); }
  .front-mark .name { font-family: "Open Sans", Arial, sans-serif; font-weight: 600; font-size: 46px; color: var(--sun-yellow); letter-spacing: 0.5px; }
  .front-url { position: absolute; left: 0; right: 0; top: 297px; text-align: center; color: var(--white); font-size: 13.5px; letter-spacing: 3.2px; }

  /* Back */
  .card-back { top: 493px; height: 342px; background: var(--paper); }
  .wave { position: absolute; inset: 0; }
  .dentists { position: absolute; right: 34px; top: 42px; text-align: right; font-family: "Roboto Condensed", Arial, sans-serif; font-weight: 700; font-size: 21px; line-height: 25px; color: var(--sun-yellow); text-transform: uppercase; }
  .practice-mark { position: absolute; left: 40px; top: 60px; }
  .practice-mark .dot { display: block; width: 34px; height: 34px; border-radius: 50%; background: var(--sun-yellow); margin: 0 0 10px 88px; }
  .practice-mark .name { font-family: "Open Sans", Arial, sans-serif; font-weight: 600; font-size: 30px; line-height: 32px; color: var(--sun-yellow); }
  .practice-mark .name .sub { display: block; font-size: 20px; line-height: 24px; }
  .contact { position: absolute; right: 34px; top: 211px; text-align: right; color: var(--white); font-size: 14px; line-height: 18px; font-style: normal; }
  .contact .line { display: flex; justify-content: flex-end; align-items: center; gap: 5px; }
  .contact .phone { margin-top: 9px; }
  .contact .web { margin-top: 2px; }
  .contact svg { width: 13px; height: 13px; }
</style>
</head>
<body>
  <section class="card card-front" aria-label="Card front">
    <div class="front-mark"><span class="dot"></span><span class="name">Maplebrook</span></div>
    <p class="front-url">www.maplebrookkidsdental.example</p>
  </section>

  <section class="card card-back" aria-label="Card back">
    <svg class="wave" viewBox="0 0 600 342" preserveAspectRatio="none" aria-hidden="true">
      <path d="M90,279 C260,264 440,160 600,127 L600,146 C450,175 300,270 160,278 C130,280 105,280 90,279 Z" fill="var(--magenta)"/>
      <path d="M0,222 C40,268 90,281 160,278 C300,270 450,175 600,146 L600,342 L0,342 Z" fill="var(--sun-yellow)"/>
      <path d="M0,222 C40,268 90,281 160,278 C300,270 450,175 600,146" fill="none" stroke="var(--white)" stroke-width="3"/>
    </svg>

    <div class="dentists">
      <p>Mei-Ran Tsai, DMD</p>
      <p>Corinne Walbeck, DMD</p>
    </div>

    <div class="practice-mark">
      <span class="dot"></span>
      <p class="name">Maplebrook<span class="sub">Pediatric Dentistry</span></p>
    </div>

    <address class="contact">
      <p>Maplebrook Pediatric Dentistry</p>
      <p>482 Quarry Lane</p>
      <p>Suite 517, Ashvale, PA 17580</p>
      <p class="line phone">717.555.0193
        <svg viewBox="0 0 24 24" aria-hidden="true"><path fill="#fff" d="M6.6 10.8c1.4 2.8 3.8 5.1 6.6 6.6l2.2-2.2c.3-.3.7-.4 1-.2 1.1.4 2.3.6 3.6.6.6 0 1 .4 1 1V20c0 .6-.4 1-1 1C10.6 21 3 13.4 3 4c0-.6.4-1 1-1h3.5c.6 0 1 .4 1 1 0 1.3.2 2.5.6 3.6.1.3 0 .7-.2 1z"/></svg>
      </p>
      <p class="line web">maplebrookkidsdental.example
        <svg viewBox="0 0 24 24" aria-hidden="true"><circle cx="12" cy="12" r="10" fill="#fff"/><path d="M2 12h20M12 2c3 3 3 17 0 20M12 2c-3 3-3 17 0 20" fill="none" stroke="var(--sun-yellow)" stroke-width="1.6"/></svg>
      </p>
    </address>
  </section>
</body>
</html>
```